Birchwell Agency Condominium mail merge

We need a marketing proposal letter design to do a mail merge to potential e customers. We included our logo and an example of my miserable attempt to create a template. We are looking for a modern and attractive proposal template. Here is our website https://www.birchwellagency.example to be used for any additional information needed about us and our services.

Target Market(s)

New prospects

Industry/Entity Type

Insurance Agency

Requirements
Must have
• My project must have a modern professional look with merge fields similar to the file uploaded with this project.
Nice to have
• it would like have a condominium and a car icon graphic depicting there is additional discounts for both quotes bundled.
Should not have
• My project should not have any other logos or company name

```html
<!DOCTYPE html>
<html lang="en">
<head>
<meta charset="utf-8">
<title>Birchwell Agency Letterhead</title>
<link href="https://fonts.googleapis.com/css2?family=Open+Sans:wght@400;600;700&family=Source+Sans+3:wght@400&family=Arimo:wght@700&display=swap" rel="stylesheet">
<style>
  :root {
    --green: #3db049;
    --orange: #f58220;
    --ink: #333333;
    --heading: #111111;
    --paper: #ffffff;
    --backdrop: #e6e6e6;
    --band: #ebebeb;
  }
  * { margin: 0; padding: 0; box-sizing: border-box; }
  html, body { width: 1059px; height: 1200px; overflow: hidden; background: var(--backdrop); }
  .letterhead {
    position: absolute; left: 221px; top: 130px;
    width: 653px; height: 922px; background: var(--paper);
    overflow: hidden;
  }
  .brand {
    position: absolute; left: 52px; top: 52px;
    display: flex; align-items: center; gap: 9px;
    font-family: "Open Sans", sans-serif; font-weight: 700;
    font-size: 23px; color: var(--green); letter-spacing: -0.3px; white-space: nowrap;
  }
  .brand-dot { width: 16px; height: 16px; border-radius: 50%; background: var(--orange); flex: none; }
  .contact { position: absolute; left: 485px; top: 43px; font-family: "Open Sans", sans-serif; white-space: nowrap; }
  .contact-id { border-left: 1.2px solid var(--green); padding-left: 8px; line-height: 12px; }
  .contact-name { font-size: 10.5px; font-weight: 700; color: var(--green); }
  .contact-role { font-size: 9.8px; color: var(--orange); }
  .contact-line { display: flex; align-items: center; gap: 5px; font-size: 9.8px; line-height: 13px; color: var(--ink); margin-top: 1px; }
  .contact-line:first-of-type { margin-top: 6px; }
  .contact-line svg { width: 8px; height: 8px; fill: var(--green); flex: none; }
  .letter { position: absolute; left: 56px; top: 211px; width: 539px; }
  .salutation { font-family: "Arimo", sans-serif; font-weight: 700; font-size: 14.5px; line-height: 18px; color: var(--heading); margin-bottom: 18px; }
  .letter p {
    font-family: "Source Sans 3", sans-serif; font-size: 13.7px; line-height: 17.1px;
    color: var(--ink); text-align: justify; margin-bottom: 17.1px; letter-spacing: -0.1px;
  }
  .signature {
    position: absolute; left: 57px; top: 642px; width: 102px; height: 50px;
    background: linear-gradient(135deg, #f2f2f2, #dcdcdc); border-radius: 3px;
  }
  .footer-wave { position: absolute; left: 0; bottom: 0; width: 653px; height: 46px; display: block; }
  .footer-url { font-family: "Open Sans", sans-serif; font-size: 12.5px; letter-spacing: 1.4px; fill: #ffffff; }
</style>
</head>
<body>
<main class="letterhead">
  <div class="brand"><span class="brand-dot"></span>Birchwell Agency</div>

  <div class="contact">
    <div class="contact-id">
      <div class="contact-name">Daniel Harlow</div>
      <div class="contact-role">Agency Principal</div>
    </div>
    <div class="contact-line">
      <svg viewBox="0 0 24 24"><path d="M6.6 10.8a15.1 15.1 0 0 0 6.6 6.6l2.2-2.2c.3-.3.7-.4 1-.2 1.1.4 2.3.6 3.6.6.6 0 1 .4 1 1V20c0 .6-.4 1-1 1A17 17 0 0 1 3 4c0-.6.4-1 1-1h3.5c.6 0 1 .4 1 1 0 1.3.2 2.5.6 3.6.1.3 0 .7-.2 1z"/></svg>
      555-014-2280
    </div>
    <div class="contact-line">
      <svg viewBox="0 0 24 24"><path d="M2 5h20v14H2z M2 5l10 8 10-8" stroke="#fff" stroke-width="1.5"/></svg>
      daniel@birchwellagency.example
    </div>
  </div>

  <section class="letter">
    <h1 class="salutation">Dear Mr. Carter,</h1>
    <p>Lorem Ipsum is simply dummy text of the printing and typesetting industry. Lorem Ipsum has been the industry's standard dummy text ever since the 1500s, when an unknown printer took a galley of type and scrambled it to make a type specimen book. It has survived not only five centuries, but also the leap into electronic typesetting, remaining essentially unchanged.</p>
    <p>The standard chunk of Lorem Ipsum used since the 1500s is reproduced below for those interested. Sections 1.10.32 and 1.10.33 from "de Finibus Bonorum et Malorum" by Cicero are also reproduced in their exact original form, accompanied by English versions from the 1914 translation by H. Rackham</p>
    <p>Lorem Ipsum is simply dummy text of the printing and typesetting industry. Lorem Ipsum has been the industry's standard dummy text ever since the 1500s, when an unknown printer took a galley of type and scrambled it to make a type specimen book. It has survived not only five centuries, but also the leap into electronic typesetting, remaining essentially unchanged. It was popularised in the</p>
    <p>The standard chunk of Lorem Ipsum used since the 1500s is reproduced below for those interested. Sections 1.10.32 and 1.10.33 from "de Finibus Bonorum et Malorum" by Cicero are also reproduced in their exact original form, accompanied by English versions from the 1914 translation by H. Rackham</p>
  </section>

  <div class="signature" role="img" aria-label="Handwritten signature of the agency principal"></div>

  <svg class="footer-wave" viewBox="0 0 816 57" aria-hidden="true">
    <path d="M190,57 C300,40 420,10 600,8 C680,8 760,25 816,44 L816,57 Z" fill="var(--band)"/>
    <path d="M0,24 C250,38 450,0 620,2 C700,3 780,25 816,40 L816,43 C760,24 680,7 600,7 C420,9 300,40 190,57 L0,57 Z" fill="var(--green)"/>
    <path d="M250,57 C380,30 520,14 620,14 C700,14 745,38 760,57 Z" fill="var(--orange)"/>
    <text class="footer-url" x="514" y="41" text-anchor="middle">www.birchwellagency.example</text>
  </svg>
</main>
</body>
</html>
```